Business Card - connecting 2 souls and beggining the journey of self discovery

Logo on the front
with tag line

On the back list of services and contact details

Seminars
workshops
Coaching
podcasts

Darren Whitlow
Health & Wellbeing Life Coach
0491 372 615
darren@brightcoreliving.example
brightcoreliving.example

Industry/Entity Type

Life Coaching

Contact Information for Business Card

I like the use of colour from the logo to be used. I'm not a fan of white.

Requirements
Must have
• My tagline: The journey home starts with you
Nice to have
• Use of colour that is in the mind body soul logo

```html
<!DOCTYPE html>
<html lang="en">
<head>
<meta charset="utf-8">
<title>Brightcore Living – Business Card</title>
<link href="https://fonts.googleapis.com/css2?family=Source+Sans+3:wght@400;600;700&display=swap" rel="stylesheet">
<style>
  :root {
    --backdrop: #c6c6c6;
    --card-front: #7f8284;
    --card-back: #ffffff;
    --text-light: #ffffff;
    --text-grey: #7d7f82;
    --name-green: #6cbd7c;
    --icon-orange: #f0a020;
    --mark-coral: #ee7a6a;
    --band-purple: #7a4a9f;
    --band-rose: #bf7a98;
    --band-yellow: #f1cf52;
    --dot-yellow: #f3b526;
  }
  * { margin: 0; padding: 0; box-sizing: border-box; }
  html, body {
    width: 1200px; height: 947px; overflow: hidden;
    background: var(--backdrop);
    font-family: "Source Sans 3", "Helvetica Neue", Arial, sans-serif;
  }
  .card {
    position: absolute; left: 263px; width: 674px; height: 385px; overflow: hidden;
  }
  .card--front { top: 81px; background: var(--card-front); }
  .card--back { top: 482px; background: var(--card-back); }

  .brand-mark {
    position: absolute; border-radius: 50%; background: var(--mark-coral);
  }
  .card--front .brand-mark { left: 276px; top: 99px; width: 128px; height: 128px; }
  .card--front .brand-name {
    position: absolute; left: 0; right: 0; top: 252px; text-align: center;
    color: var(--text-light); font-size: 31px; font-weight: 400; letter-spacing: -0.3px;
  }
  .tagline {
    position: absolute; left: 0; right: 0; top: 335px; text-align: center;
    color: var(--text-light); font-size: 16px; font-weight: 400;
  }

  .card--back .brand-mark { left: 490px; top: 35px; width: 78px; height: 78px; }
  .card--back .brand-name {
    position: absolute; right: 36px; top: 129px; line-height: 26px;
    color: var(--text-grey); font-size: 20px; font-weight: 400; letter-spacing: -0.2px;
  }
  .person { position: absolute; left: 35px; top: 188px; }
  .person__name { color: var(--name-green); font-size: 24px; font-weight: 600; line-height: 26px; }
  .person__role { color: var(--text-grey); font-size: 16px; font-weight: 600; line-height: 20px; margin-top: 2px; }

  .contact { position: absolute; left: 35px; top: 261px; list-style: none; }
  .contact li {
    display: flex; align-items: center; gap: 6px; height: 22px;
    color: var(--text-grey); font-size: 16px; font-weight: 600;
  }
  .contact svg { width: 14px; height: 14px; flex: none; }

  .services {
    position: absolute; left: 0; right: 0; bottom: 0; height: 36px;
    background: linear-gradient(90deg, var(--band-purple) 0%, var(--band-purple) 22%, var(--band-rose) 55%, var(--band-yellow) 100%);
    display: flex; align-items: center; padding-left: 35px; list-style: none;
    color: var(--text-light); font-size: 17px;
  }
  .services li + li::before {
    content: "•"; color: var(--dot-yellow); margin: 0 8px; font-size: 14px;
  }
</style>
</head>
<body>
  <section class="card card--front">
    <div class="brand-mark"></div>
    <p class="brand-name">Brightcore Living</p>
    <p class="tagline">The journey home starts with you</p>
  </section>

  <section class="card card--back">
    <div class="brand-mark"></div>
    <p class="brand-name">Brightcore Living</p>

    <div class="person">
      <p class="person__name">Darren Whitlow</p>
      <p class="person__role">Life Coach</p>
    </div>

    <ul class="contact">
      <li>
        <svg viewBox="0 0 24 24" aria-hidden="true"><path fill="var(--icon-orange)" d="M6.6 10.8a15.1 15.1 0 0 0 6.6 6.6l2.2-2.2a1 1 0 0 1 1-.25 11.4 11.4 0 0 0 3.6.57 1 1 0 0 1 1 1V20a1 1 0 0 1-1 1A17 17 0 0 1 3 4a1 1 0 0 1 1-1h3.5a1 1 0 0 1 1 1c0 1.250.2 2.450.57 3.57a1 1 0 0 1-.25 1z"/></svg>
        0491 372 615
      </li>
      <li>
        <svg viewBox="0 0 24 24" aria-hidden="true"><rect x="2.5" y="5" width="19" height="14" fill="none" stroke="var(--icon-orange)" stroke-width="2"/><path d="M3 6l9 7 9-7" fill="none" stroke="var(--icon-orange)" stroke-width="2"/></svg>
        darren@brightcoreliving.example
      </li>
      <li>
        <svg viewBox="0 0 24 24" aria-hidden="true"><g fill="none" stroke="var(--icon-orange)" stroke-width="2"><circle cx="12" cy="12" r="9.5"/><ellipse cx="12" cy="12" rx="4" ry="9.5"/><path d="M2.5 12h19M4 7h16M4 17h16"/></g></svg>
        brightcoreliving.example
      </li>
    </ul>

    <ul class="services">
      <li>Seminars</li>
      <li>Workshops</li>
      <li>Coaching</li>
      <li>Podcasts</li>
    </ul>
  </section>
</body>
</html>
```